New bussiness card, using company logo.
Lionel Brisk
Manager/Director
Brisk Property Developments
Po Box 5347
Thuringowa Central
Qld
0491 638 205
lionel@briskpropertydevelopments
eye catching, vibrant colours, professional

```html
<!DOCTYPE html>
<html lang="en">
<head>
<meta charset="utf-8">
<title>Brisk Property Developments – Business Cards</title>
<link rel="stylesheet" href="https://fonts.googleapis.com/css2?family=PT+Sans:wght@400;700&display=swap">
<style>
  :root {
    --backdrop: #2b2a29;
    --card-white: #ffffff;
    --brand-red: #e1252b;
    --brand-green: #6cbd45;
    --green-light: #8cc63f;
    --green-deep: #5fb245;
    --ink-grey: #555555;
    --ink-dark: #222222;
  }
  * { margin: 0; padding: 0; box-sizing: border-box; }
  html, body { width: 1200px; height: 736px; overflow: hidden; }
  body {
    background: var(--backdrop);
    font-family: "PT Sans", "Segoe UI", Arial, sans-serif;
    position: relative;
  }
  .card {
    position: absolute;
    width: 556px;
    height: 316px;
    border-radius: 22px;
    overflow: hidden;
  }
  .card--contact { left: 27px; top: 36px; background: var(--card-white); }
  .card--red { left: 609px; top: 36px; background: var(--brand-red); }
  .card--white-logo { left: 27px; top: 386px; background: var(--card-white); }
  .card--green { left: 612px; top: 386px; background: linear-gradient(90deg, var(--green-light), var(--green-deep)); }

  .brand-name {
    position: absolute;
    left: 0; right: 0;
    text-align: center;
    font-weight: 700;
    line-height: 1.1;
  }
  .card--contact .brand-name { top: 78px; font-size: 26px; color: var(--brand-red); }
  .card--red .brand-name { top: 130px; font-size: 38px; color: var(--card-white); }
  .card--white-logo .brand-name { top: 122px; font-size: 38px; color: var(--brand-red); }
  .card--green .brand-name { top: 150px; font-size: 34px; color: var(--card-white); }

  .person {
    position: absolute;
    top: 176px; left: 0; right: 0;
    text-align: center;
  }
  .person__name { color: var(--brand-red); font-weight: 700; font-size: 20px; }
  .person__role { color: var(--ink-grey); font-size: 15px; }

  .contact-band { position: absolute; left: 0; top: 0; width: 556px; height: 316px; }

  .contact {
    position: absolute;
    top: 258px;
    color: var(--card-white);
    font-size: 13px;
    line-height: 20px;
  }
  .contact--postal { right: 345px; text-align: right; }
  .contact--direct { left: 236px; }
  .contact__divider {
    position: absolute;
    left: 223px; top: 259px;
    width: 1px; height: 38px;
    background: var(--card-white);
  }
  .contact__line { display: flex; align-items: center; gap: 6px; }
  .contact__line svg { width: 11px; height: 11px; }

  .website {
    position: absolute;
    left: 0; right: 0;
    text-align: center;
    font-size: 15px;
    letter-spacing: 1px;
  }
  .card--red .website { top: 274px; color: var(--card-white); }
  .card--white-logo .website { top: 274px; color: var(--ink-dark); }
  .card--green .website { top: 274px; color: var(--card-white); }
</style>
</head>
<body>

  <section class="card card--contact">
    <div class="brand-name">Brisk Property Developments</div>
    <div class="person">
      <span class="person__name">Lionel Brisk,</span>
      <span class="person__role">Manager/Director</span>
    </div>
    <svg class="contact-band" viewBox="0 0 556 316" aria-hidden="true">
      <path d="M0,276 Q278,183 556,270 L556,316 L0,316 Z" fill="var(--brand-red)"/>
      <path d="M0,268 Q278,166 556,262" fill="none" stroke="var(--brand-green)" stroke-width="3"/>
    </svg>
    <div class="contact contact--postal">
      <div>Po Box 5347</div>
      <div>Elderby Central , Vic</div>
    </div>
    <div class="contact__divider"></div>
    <div class="contact contact--direct">
      <div class="contact__line">
        <svg viewBox="0 0 12 12"><path d="M3,1 L5,3.5 L4,5 Q5.5,7 7,8 L8.5,7 L11,9 L9.5,11 Q4,10 1,2.5 Z" fill="#fff"/></svg>
        <span>0491 638 205</span>
      </div>
      <div class="contact__line">
        <svg viewBox="0 0 12 12"><rect x="1" y="3" width="10" height="7" fill="#fff"/><path d="M1,3 L6,7 L11,3" fill="none" stroke="var(--brand-red)" stroke-width="1"/></svg>
        <span>lionel@briskpropertydevelopments.com</span>
      </div>
    </div>
  </section>

  <section class="card card--red">
    <div class="brand-name">Brisk Property Developments</div>
    <div class="website">www.briskpropertydevelopments.com</div>
  </section>

  <section class="card card--white-logo">
    <div class="brand-name">Brisk Property Developments</div>
    <div class="website">www.briskpropertydevelopments.com</div>
  </section>

  <section class="card card--green">
    <div class="brand-name">Brisk Property Developments</div>
    <div class="website">www.briskpropertydevelopments.com</div>
  </section>

</body>
</html>
```